Dietitian needs awesome business card

I need a contemporary design that's eye catching but professional.
My card is to given to doctors, specialists and patients alike.
I manage patients with chronic diseases
I have uploaded my logo and current business card, I would also like the other Certified Clinical Nutritionist logo incorporated into the design

Target Market(s)

Doctors, specialists and patients

Industry/Entity Type

Healthcare

Contact Information for Business Card

www.brightfieldnutrition.com.au
Ph: 0427 561 903
Fax: 6457 2183
email: marcus.k.diet@fernmail.com
Space on the back of the card with: Appointment date, Appointment time and appointment location

Font styles to use
Serif

Colors
fbee3e
876aae
ffc214

Requirements
Must have
• My Logo
• Certified Clinical Nutritionist Logo
• My 4 locations - Pinebrook Medical Centre, North Corrin Health, Hollis Medical, Ashcombe Doctors Surgery
Nice to have
• I like the colours in my current business card

```html
<!DOCTYPE html>
<html lang="en">
<head>
<meta charset="utf-8">
<title>Brightfield Nutrition &amp; Dietetics – Business Card</title>
<link href="https://fonts.googleapis.com/css2?family=Arimo:wght@400;700&display=swap" rel="stylesheet">
<style>
  :root{
    --stage:#2b2b2d;
    --card:#ffffff;
    --ink-blue:#1f3f9e;
    --royal:#2430a0;
    --sky:#1a8fe0;
    --leaf:#8cc63f;
    --line:#b9bcc4;
    --label:#2b4aa8;
    --text-grey:#4a4d55;
    --badge:#f47a20;
  }
  *{margin:0;padding:0;box-sizing:border-box}
  html,body{width:1200px;height:950px;overflow:hidden;background:var(--stage)}
  body{font-family:"Arimo",Arial,sans-serif;position:relative}

  .card{position:absolute;left:220px;width:760px;height:430px;background:var(--card);overflow:hidden;box-shadow:0 6px 18px rgba(0,0,0,.35)}
  .card--back{top:30px}
  .card--front{top:490px}

  .brand{position:absolute;display:flex;align-items:center;gap:14px;color:var(--ink-blue)}
  .brand__dot{width:58px;height:58px;border-radius:50%;background:var(--sky);flex:none}
  .brand__name{font-size:34px;font-weight:400;line-height:1.05}
  .brand__name small{display:block;font-size:19px}

  /* back */
  .card--back .brand{left:40px;top:120px}
  .badge{position:absolute;right:40px;top:28px;width:150px;height:74px;background:var(--badge)}
  .fill-line{position:absolute;left:290px;right:40px;height:1px;background:var(--line)}
  .field{position:absolute;font-size:19px;color:var(--label);display:flex;align-items:flex-end;gap:8px}
  .field__rule{height:1px;background:var(--line);margin-bottom:4px}
  .ampm{position:absolute;right:40px;top:228px;font-size:14px;color:var(--label)}
  .locations{position:absolute;list-style:none;font-size:18px;color:var(--text-grey)}
  .locations li{display:flex;align-items:center;gap:10px;margin-bottom:6px}
  .locations li::before{content:"";width:14px;height:14px;border:1.5px solid var(--label);flex:none}

  /* front */
  .card--front .brand{left:60px;top:160px}
  .sweep{position:absolute;inset:0}
  .contact{position:absolute;right:34px;top:148px;text-align:right;color:#fff}
  .contact__name{font-size:24px;font-weight:700}
  .contact__role{font-size:16px;font-weight:700;margin:4px 0 14px}
  .contact__row{display:flex;justify-content:flex-end;align-items:center;gap:10px;font-size:15px;line-height:26px}
  .contact__row svg{width:16px;height:16px;flex:none}
</style>
</head>
<body>

<section class="card card--back" aria-label="Appointment side">
  <div class="brand">
    <span class="brand__dot"></span>
    <span class="brand__name">Brightfield<small>Nutrition &amp; Dietetics</small></span>
  </div>
  <div class="badge" role="img" aria-label="Certified Clinical Nutritionist accreditation badge"></div>

  <div class="fill-line" style="top:130px"></div>
  <div class="fill-line" style="top:180px"></div>
  <div class="fill-line" style="top:230px;left:290px;right:120px"></div>
  <span class="ampm">AM/PM</span>

  <div class="field" style="left:40px;top:300px"><span>Date :</span><span class="field__rule" style="width:230px"></span></div>
  <div class="field" style="left:400px;top:250px"><span>Time :</span><span class="field__rule" style="width:240px"></span></div>

  <ul class="locations" style="left:40px;top:345px">
    <li>Pinebrook Medical Centre</li>
    <li>North Corrin Health</li>
  </ul>
  <ul class="locations" style="left:400px;top:290px">
    <li>Ashcombe Doctors Surgery</li>
    <li>Hollis Medical</li>
  </ul>
</section>

<section class="card card--front" aria-label="Contact side">
  <svg class="sweep" viewBox="0 0 760 430" preserveAspectRatio="none" aria-hidden="true">
    <defs>
      <linearGradient id="blueField" x1="0" y1="0" x2="1" y2="1">
        <stop offset="0" stop-color="#1a8fe0"/>
        <stop offset="0.55" stop-color="#2457c4"/>
        <stop offset="1" stop-color="#2430a0"/>
      </linearGradient>
    </defs>
    <path d="M760 0 Q440 40 380 430 L760 430 Z" fill="var(--leaf)"/>
    <path d="M760 12 Q456 52 398 430 L760 430 Z" fill="#fff"/>
    <path d="M760 20 Q468 60 410 430 L760 430 Z" fill="url(#blueField)"/>
  </svg>

  <div class="brand">
    <span class="brand__dot"></span>
    <span class="brand__name">Brightfield<small>Nutrition &amp; Dietetics</small></span>
  </div>

  <div class="contact">
    <div class="contact__name">Marcus Kellaway</div>
    <div class="contact__role">Nutritionist &amp; Chef</div>
    <div class="contact__row">0427 561 903
      <svg viewBox="0 0 24 24" fill="#fff"><path d="M6.6 10.8a15 15 0 0 0 6.6 6.6l2.2-2.2a1 1 0 0 1 1-.25 11 11 0 0 0 3.6.6 1 1 0 0 1 1 1V20a1 1 0 0 1-1 1A17 17 0 0 1 3 4a1 1 0 0 1 1-1h3.5a1 1 0 0 1 1 1 11 11 0 0 0 .6 3.6 1 1 0 0 1-.25 1z"/></svg>
    </div>
    <div class="contact__row">6457 2183
      <svg viewBox="0 0 24 24" fill="#fff"><rect x="6" y="2" width="12" height="6"/><rect x="2" y="9" width="20" height="9" rx="2"/><rect x="6" y="15" width="12" height="7" fill="#2457c4" stroke="#fff" stroke-width="2"/></svg>
    </div>
    <div class="contact__row">marcus.k.diet@fernmail.com
      <svg viewBox="0 0 24 24"><rect x="2" y="5" width="20" height="14" fill="#fff"/><path d="M2 5l10 8 10-8" fill="none" stroke="#2457c4" stroke-width="2"/></svg>
    </div>
    <div class="contact__row">www.brightfieldnutrition.com.au
      <svg viewBox="0 0 24 24" fill="none" stroke="#fff" stroke-width="2"><circle cx="12" cy="12" r="9"/><path d="M3 12h18M12 3c3 3 3 15 0 18M12 3c-3 3-3 15 0 18"/></svg>
    </div>
  </div>
</section>

</body>
</html>
```